Business Card - Business Consultancy

Newly Established Company, specializing in Business Consultancy, Human Resource Management, Talent Acquisition and Payroll Solutions.

We need a Business card design which portrays "elegance" and a very sleek yet business-like design. We would like a nice blue trimming (which goes well with the logo) to separate the content of the business card at the top. We would also like to see the design using the color silver either as a background or incorporated into it.

The final design should be a Business card which has colors matching the logo; a nice font; the above-mentioned specifics that adheres to the theme of "a stylish and professional business"

FYI: please do not have too fanciful designs.

Industry/Entity Type

Business Consultant

Contact Information for Business Card

Darren Lim
Business Development Director
Arbor Talent Consulting Private Limited
27 Wexley Street, #05-03B
Harbourgate Trade Building
Singapore 059317
Mobile : (+65) 98354417
Email : dlim@arbortalent-advisory.com
Alternative : arbortalentadvisory@mailbox-example.com

Requirements
Must have
• Nice Blue Trimming matching Logo which separates content, see attached
• Design incorporates either a silver background or the use of the color silver
Should not have
• No Fanciful Designs
• No Childish Designs
• No Overly Complicated Designs

```html
<!DOCTYPE html>
<html lang="en">
<head>
<meta charset="utf-8">
<title>Arbor Talent Consulting – Business Cards</title>
<link rel="stylesheet" href="https://fonts.googleapis.com/css2?family=Open+Sans:wght@400;600;700&display=swap">
<style>
  :root {
    --page: #e9ecef;
    --paper: #ffffff;
    --brand-blue: #0a7ec8;
    --brand-green: #7cc02a;
    --silver: #c0c4c8;
    --ink: #2b2b2b;
    --on-blue: #ffffff;
    --font: "Open Sans", Arial, sans-serif;
  }
  * { box-sizing: border-box; margin: 0; padding: 0; }
  html, body {
    width: 1200px; height: 900px; overflow: hidden;
    background: var(--page);
    font-family: var(--font);
  }
  .card {
    position: absolute;
    width: 590px; height: 365px;
    background: var(--paper);
    box-shadow: 0 6px 18px rgba(0,0,0,.18);
    overflow: hidden;
  }
  .card--front { left: 77px; top: 33px; }
  .card--back  { left: 375px; top: 500px; }
  .card__bands { position: absolute; inset: 0; width: 100%; height: 100%; }
  .band--blue { fill: var(--brand-blue); }
  .band--green { fill: var(--brand-green); }
  .band--silver { fill: none; stroke: var(--silver); stroke-width: 3; }

  .brand {
    position: absolute; top: 40px; left: 150px;
    display: flex; align-items: center; gap: 16px;
  }
  .brand__dot {
    width: 88px; height: 88px; border-radius: 50%;
    background: var(--brand-blue);
  }
  .brand__name {
    color: var(--ink); font-weight: 700;
    font-size: 30px; line-height: 1.1; letter-spacing: .5px;
  }

  .person {
    position: absolute; left: 322px; top: 207px; color: var(--on-blue);
  }
  .person__name { font-size: 21px; font-weight: 600; line-height: 1.2; }
  .person__title { font-size: 15px; line-height: 1.4; }
  .address {
    position: absolute; left: 322px; top: 276px;
    color: var(--on-blue); font-size: 15px; line-height: 25px; font-style: normal;
  }
  .contacts {
    position: absolute; right: 290px; top: 247px;
    list-style: none; color: var(--on-blue);
    font-size: 13px; line-height: 25px; text-align: right;
  }
  .contacts li { display: flex; align-items: center; justify-content: flex-end; gap: 7px; white-space: nowrap; }
  .contacts svg { width: 12px; height: 12px; fill: var(--on-blue); flex: none; }
  .contacts .icon-mail__flap { fill: none; stroke: var(--brand-blue); stroke-width: 2; }

  .tagline {
    position: absolute; left: 0; right: 0; top: 255px;
    padding: 0 110px;
    color: var(--on-blue); font-size: 19px; font-weight: 700;
    line-height: 25px; text-align: center;
  }
</style>
</head>
<body>

<section class="card card--front">
  <svg class="card__bands" viewBox="0 0 590 365" aria-hidden="true">
    <polygon class="band--green" points="0,170 403,170 378,194 0,194"/>
    <polygon class="band--blue" points="0,199 380,199 413,163 590,163 590,365 0,365"/>
    <polyline class="band--silver" points="0,196.5 378,196.5 407,165.5"/>
  </svg>
  <div class="brand">
    <span class="brand__dot"></span>
    <span class="brand__name">Arbor Talent<br>Consulting</span>
  </div>
  <div class="person">
    <p class="person__name">Darren Lim</p>
    <p class="person__title">Business Development Director</p>
  </div>
  <ul class="contacts">
    <li>(+65) 98354417
      <svg viewBox="0 0 24 24"><path d="M6.6 10.8a15.2 15.2 0 0 0 6.6 6.6l2.2-2.2a1 1 0 0 1 1-.25 11.4 11.4 0 0 0 3.6.57 1 1 0 0 1 1 1V20a1 1 0 0 1-1 1A17 17 0 0 1 3 4a1 1 0 0 1 1-1h3.5a1 1 0 0 1 1 1c0 1.25.2 2.45.57 3.57a1 1 0 0 1-.25 1z"/></svg>
    </li>
    <li>dlim@arbortalent-advisory.com
      <svg viewBox="0 0 24 24"><path d="M2 5h20v14H2z"/><path class="icon-mail__flap" d="M3 6l9 7 9-7"/></svg>
    </li>
    <li>arbortalentadvisory@mailbox-example.com
      <svg viewBox="0 0 24 24"><path d="M2 5h20v14H2z"/><path class="icon-mail__flap" d="M3 6l9 7 9-7"/></svg>
    </li>
  </ul>
  <address class="address">
    27 Wexley Street, #05-03B<br>
    Harbourgate Trade Building<br>
    Singapore 059317
  </address>
</section>

<section class="card card--back">
  <svg class="card__bands" viewBox="0 0 590 365" aria-hidden="true">
    <polygon class="band--green" points="0,170 403,170 378,194 0,194"/>
    <polygon class="band--blue" points="0,199 380,199 413,163 590,163 590,365 0,365"/>
    <polyline class="band--silver" points="0,196.5 378,196.5 407,165.5"/>
  </svg>
  <div class="brand">
    <span class="brand__dot"></span>
    <span class="brand__name">Arbor Talent<br>Consulting</span>
  </div>
  <p class="tagline">Recruitment | HR Solutions | Business Consultancy</p>
</section>

</body>
</html>
```